web hosting reseller site, E-COMMERCE FUNCTIONALITY, AND MONTHLY PAYMENT INTERGRATION

hie there , i need a web hosting reseller site , 5 pages seo friendly , responsive and mobile friendly, i have a seller domain , basic content uploaded , design theme . i will be selling web hosting packages and domain names , i will also offer web design services and development . my project is so simple , the basic pages have content submitted already ,etc HOME, ABOUT, CONTACT US, BLOG POST .
Target Market(s)
5
Industry/Entity Type
web hosting
Coding
Coded - Design and coding required
Number of Pages Required
5+ page
Font styles to use
Requirements
Must have
- e commerce functionality, blog post, knowledge base , faq ,
Should not have
- affiliate links , subscription plugins

```html
<!DOCTYPE html>
<html lang="en">
<head>
<meta charset="utf-8">
<title>NovaHost – FAQ's</title>
<link rel="stylesheet" href="https://fonts.googleapis.com/css2?family=Poppins:wght@400;500;600&family=Tinos:wght@700&display=swap">
<style>
:root{
  --sky:#c5e9f7;
  --blue:#0a8fd6;
  --ink:#111111;
  --text:#333333;
  --muted:#4a4a4a;
  --border:#dcdcdc;
  --hero:#22164a;
  --foot-left:#00a8e2;
  --foot-right:#0495d8;
  --white:#ffffff;
}
*{box-sizing:border-box;margin:0;padding:0}
html,body{width:1200px;height:2685px;overflow:hidden}
body{font-family:"Poppins",sans-serif;color:var(--text);background:var(--white)}
a{color:inherit;text-decoration:none}

.topbar{height:59px;background:var(--sky);display:flex;align-items:center;justify-content:space-between;padding:0 75px}
.topbar-phone{display:flex;align-items:center;gap:8px;color:var(--blue);font-weight:600;font-size:19px;letter-spacing:.5px}
.topbar-links{display:flex;align-items:center;gap:10px;font-size:16px;color:#222}
.topbar-links span.sep{margin:0 4px}
.topbar-links .item{display:flex;align-items:center;gap:7px}

.header{height:108px;display:flex;align-items:center;justify-content:space-between;padding:0 75px}
.logo{font-family:"Tinos",serif;font-weight:700;font-size:50px;color:var(--ink);letter-spacing:.5px}
.nav{display:flex;gap:31px;font-family:"Tinos",serif;font-weight:700;font-size:18.5px;color:var(--ink);letter-spacing:.3px}
.nav .active{color:var(--blue)}

.hero{height:511px;background:var(--hero);position:relative;overflow:hidden}
.hero-art{position:absolute;left:470px;top:0;width:730px;height:511px;background:radial-gradient(ellipse at 62% 58%,#6a5cf0 0%,#3d3aa8 30%,#2b2170 60%,rgba(34,22,74,0) 85%)}
.hero h1{position:absolute;left:73px;top:217px;color:var(--white);font-size:70px;font-weight:600;letter-spacing:2px}

.faq{padding:64px 75px 0}
.faq-title{text-align:center;font-family:"Tinos",serif;font-weight:700;font-size:64px;color:var(--ink);letter-spacing:1px;line-height:1;margin-bottom:44px}
.faq-title span{color:var(--blue)}
.faq-item{border:1px solid var(--border);margin-bottom:16px}
.faq-q{height:58px;display:flex;align-items:center;justify-content:space-between;padding:0 22px;font-weight:600;font-size:19px;color:var(--muted)}
.faq-item.open .faq-q{height:60px;padding-top:6px;color:var(--blue)}
.faq-a{padding:0 50px 11px 22px;font-size:16.1px;line-height:35px;color:var(--text)}

.footer{position:absolute;top:2213px;left:0;width:1200px;height:472px;display:flex}
.foot-brand{width:341px;background:var(--foot-left);padding:118px 0 0 75px;color:var(--white)}
.foot-brand .logo{color:var(--white);font-size:52px;line-height:1}
.copy{font-size:14px;line-height:26px;margin-top:16px}
.foot-phone{display:flex;align-items:center;gap:8px;font-weight:600;font-size:24px;margin-top:18px;letter-spacing:.5px}
.social{display:flex;gap:26px;margin-top:22px}
.social span{width:22px;height:22px;border-radius:50%;background:var(--white)}
.foot-links{flex:1;background:var(--foot-right);display:flex;padding:74px 0 0 63px;color:var(--white)}
.col h4{font-family:"Tinos",serif;font-weight:700;font-size:24px;letter-spacing:.5px;margin-bottom:8px}
.col ul{list-style:none;font-size:15.5px}
.col.company{width:251px}
.col.company li{line-height:39.6px}
.col.services{width:270px}
.col.services li{line-height:32.3px}
.col.programs li{line-height:39.6px}
</style>
</head>
<body>
<div class="topbar">
  <div class="topbar-phone">
    <svg width="16" height="18" viewBox="0 0 16 18" aria-hidden="true"><path d="M3 1l3 3-2 2c1 3 3 5 6 6l2-2 3 3-2 3C7 16 1 10 1 3z" fill="none" stroke="currentColor" stroke-width="1.8"/></svg>
    1-800-555-0142
  </div>
  <div class="topbar-links">
    <a class="item" href="#"><svg width="13" height="15" viewBox="0 0 13 15" aria-hidden="true"><rect x="1" y="6" width="11" height="8" rx="1" fill="#0a8fd6"/><path d="M3.5 6V4a3 3 0 016 0v2" fill="none" stroke="#0a8fd6" stroke-width="1.8"/></svg>Log in</a>
    <span class="sep">/</span>
    <a class="item" href="#"><svg width="18" height="14" viewBox="0 0 18 14" aria-hidden="true"><ellipse cx="7" cy="6" rx="7" ry="5" fill="#0a8fd6"/><ellipse cx="12" cy="9" rx="6" ry="4.5" fill="#0a8fd6"/></svg>Live Chat</a>
    <span class="sep">/</span>
    <a class="item" href="#"><svg width="13" height="15" viewBox="0 0 16 18" aria-hidden="true"><path d="M3 1l3 3-2 2c1 3 3 5 6 6l2-2 3 3-2 3C7 16 1 10 1 3z" fill="none" stroke="#0a8fd6" stroke-width="1.8"/></svg>Call</a>
  </div>
</div>

<header class="header">
  <div class="logo">NovaHost</div>
  <nav class="nav">
    <a href="#">Home</a><a href="#">About</a><a href="#">Packages</a><a href="#">Programs</a><a href="#">Blog</a><a class="active" href="#">FAQ’s</a><a href="#">Careers</a><a href="#">Contact Us</a>
  </nav>
</header>

<section class="hero">
  <div class="hero-art" role="img" aria-label="Isometric illustration of a laptop, server racks and people working with hosting dashboards"></div>
  <h1>FAQ’s</h1>
</section>

<section class="faq">
  <h2 class="faq-title">Free Asking <span>Questions</span></h2>

  <div class="faq-item open">
    <div class="faq-q">Is NovaHost good for small businesses?
      <svg width="14" height="10" viewBox="0 0 14 10" aria-hidden="true"><path d="M2 2l5 5 5-5" fill="none" stroke="#0a8fd6" stroke-width="2.2"/></svg>
    </div>
    <p class="faq-a">Sed ut perspiciatis unde omnis iste natus error sit voluptatem accusantium doloremque laudantium, totam rem aperiam, eaque ipsa quae ab illo inventore veritatis et quasi architecto beatae vitae dicta sunt explicabo. Nemo enim ipsam voluptatem quia voluptas sit aspernatur aut odit aut fugit, sed quia consequuntur magni dolores eos qui ratione voluptatem sequi nesciunt.</p>
  </div>

  <div class="faq-item"><div class="faq-q">Why is NovaHost a reliable hosting company?<svg width="10" height="14" viewBox="0 0 10 14" aria-hidden="true"><path d="M2 2l5 5-5 5" fill="none" stroke="#444" stroke-width="2.2"/></svg></div></div>
  <div class="faq-item"><div class="faq-q">How do I buy a domain name on NovaHost?<svg width="10" height="14" viewBox="0 0 10 14" aria-hidden="true"><path d="M2 2l5 5-5 5" fill="none" stroke="#444" stroke-width="2.2"/></svg></div></div>
  <div class="faq-item"><div class="faq-q">How do I buy a domain name on NovaHost?<svg width="10" height="14" viewBox="0 0 10 14" aria-hidden="true"><path d="M2 2l5 5-5 5" fill="none" stroke="#444" stroke-width="2.2"/></svg></div></div>
  <div class="faq-item"><div class="faq-q">Why Choose NovaHost for SiteForge?<svg width="10" height="14" viewBox="0 0 10 14" aria-hidden="true"><path d="M2 2l5 5-5 5" fill="none" stroke="#444" stroke-width="2.2"/></svg></div></div>
  <div class="faq-item"><div class="faq-q">Is NovaHost good for small businesses?<svg width="10" height="14" viewBox="0 0 10 14" aria-hidden="true"><path d="M2 2l5 5-5 5" fill="none" stroke="#444" stroke-width="2.2"/></svg></div></div>
  <div class="faq-item"><div class="faq-q">Why is NovaHost a reliable hosting company?<svg width="10" height="14" viewBox="0 0 10 14" aria-hidden="true"><path d="M2 2l5 5-5 5" fill="none" stroke="#444" stroke-width="2.2"/></svg></div></div>
  <div class="faq-item"><div class="faq-q">How do I buy a domain name on NovaHost?<svg width="10" height="14" viewBox="0 0 10 14" aria-hidden="true"><path d="M2 2l5 5-5 5" fill="none" stroke="#444" stroke-width="2.2"/></svg></div></div>
  <div class="faq-item"><div class="faq-q">How do I buy a domain name on NovaHost?<svg width="10" height="14" viewBox="0 0 10 14" aria-hidden="true"><path d="M2 2l5 5-5 5" fill="none" stroke="#444" stroke-width="2.2"/></svg></div></div>
  <div class="faq-item"><div class="faq-q">Why Choose NovaHost for SiteForge?<svg width="10" height="14" viewBox="0 0 10 14" aria-hidden="true"><path d="M2 2l5 5-5 5" fill="none" stroke="#444" stroke-width="2.2"/></svg></div></div>
  <div class="faq-item"><div class="faq-q">Is NovaHost good for small businesses?<svg width="10" height="14" viewBox="0 0 10 14" aria-hidden="true"><path d="M2 2l5 5-5 5" fill="none" stroke="#444" stroke-width="2.2"/></svg></div></div>
  <div class="faq-item"><div class="faq-q">Why is NovaHost a reliable hosting company?<svg width="10" height="14" viewBox="0 0 10 14" aria-hidden="true"><path d="M2 2l5 5-5 5" fill="none" stroke="#444" stroke-width="2.2"/></svg></div></div>
  <div class="faq-item"><div class="faq-q">How do I buy a domain name on NovaHost?<svg width="10" height="14" viewBox="0 0 10 14" aria-hidden="true"><path d="M2 2l5 5-5 5" fill="none" stroke="#444" stroke-width="2.2"/></svg></div></div>
  <div class="faq-item"><div class="faq-q">How do I buy a domain name on NovaHost?<svg width="10" height="14" viewBox="0 0 10 14" aria-hidden="true"><path d="M2 2l5 5-5 5" fill="none" stroke="#444" stroke-width="2.2"/></svg></div></div>
  <div class="faq-item"><div class="faq-q">Why Choose NovaHost for SiteForge?<svg width="10" height="14" viewBox="0 0 10 14" aria-hidden="true"><path d="M2 2l5 5-5 5" fill="none" stroke="#444" stroke-width="2.2"/></svg></div></div>
</section>

<footer class="footer">
  <div class="foot-brand">
    <div class="logo">NovaHost</div>
    <p class="copy">© Copyright 2022 CompanyName<br>All Rights Reserved</p>
    <div class="foot-phone">
      <svg width="20" height="22" viewBox="0 0 16 18" aria-hidden="true"><path d="M3 1l3 3-2 2c1 3 3 5 6 6l2-2 3 3-2 3C7 16 1 10 1 3z" fill="none" stroke="#fff" stroke-width="1.8"/></svg>
      1-800-555-0142
    </div>
    <div class="social" aria-label="Social links"><span></span><span></span><span></span><span></span><span></span></div>
  </div>
  <div class="foot-links">
    <div class="col company">
      <h4>Company</h4>
      <ul><li>About</li><li>Careers</li><li>Contact</li><li>Terms Of Services</li><li>Privacy</li><li>Site Map</li><li>Blog</li><li>FAQ’s</li></ul>
    </div>
    <div class="col services">
      <h4>Services</h4>
      <ul><li>Web Hosting</li><li>SiteForge Hosting</li><li>ShopForge Hosting</li><li>Reseller Hosting</li><li>Cloud Hosting</li><li>Domain Names</li><li>Dedicated hosting</li><li>Site Builder</li><li>SSL</li><li>Shared hosting</li></ul>
    </div>
    <div class="col programs">
      <h4>Programs</h4>
      <ul><li>SiteForge</li><li>Affiliate</li><li>Marketing services</li><li>SiteForge guide</li></ul>
    </div>
  </div>
</footer>
</body>
</html>
```